Maple Roster Business Card for recruitment company

We are looking for a Business Card Design that incorporates our personal details and our busines name and logo. We are a specialized search consultancy that recruit Property and Construction professionals.
We would like a business card that stands out and is appealing to the Construction and Property industry as well.

Target Market(s)

people in the construction and property industry

Contact Information for Business Card

Business Name and logo

Font styles to use
Serif

Colors
0094D4
00A9DD
6FCCEA
C7EBF8
E9F6FB

Requirements
Must have
• Business name and logo as well as contact details
Should not have
• No photos of us please

```html
<!DOCTYPE html>
<html lang="en">
<head>
<meta charset="utf-8">
<title>Maple Roster – Business Card</title>
<link href="https://fonts.googleapis.com/css2?family=Questrial&family=Montserrat:wght@700&display=swap" rel="stylesheet">
<style>
  :root {
    --stage: #2b2b2b;
    --card-front: #fbfbfb;
    --card-front-shade: #ececec;
    --navy: #0b3a4f;
    --navy-deep: #06293a;
    --navy-mid: #093549;
    --ink: #2f3336;
    --logo-light: #e4e6e8;
  }
  * { box-sizing: border-box; margin: 0; padding: 0; }
  html, body {
    width: 1200px; height: 732px; overflow: hidden;
    background: var(--stage);
  }
  .canvas { position: relative; width: 1200px; height: 732px; }

  .card {
    position: absolute; top: 242px;
    width: 436px; height: 248px;
    box-shadow: 0 6px 14px rgba(0,0,0,0.45);
    overflow: hidden;
  }
  .card--front {
    left: 144px;
    background: linear-gradient(160deg, var(--card-front) 45%, var(--card-front-shade));
    color: var(--navy);
  }
  .card--back {
    left: 621px;
    background: linear-gradient(135deg, var(--navy-mid), var(--navy-deep));
  }

  .wordmark {
    position: absolute;
    font-family: "Questrial", sans-serif;
    text-transform: uppercase;
    white-space: nowrap;
    line-height: 1;
  }
  .card--front .wordmark {
    left: 17px; top: 91px;
    width: 219px;
    font-size: 28.5px; letter-spacing: -0.2px;
    color: var(--navy);
  }
  .card--front .rule {
    position: absolute; left: 17px; top: 129px;
    width: 219px; height: 1px; background: var(--navy);
  }
  .card--back .wordmark {
    left: 58px; top: 184px;
    font-size: 41.5px; letter-spacing: 0.5px;
    color: var(--logo-light);
  }

  .contact {
    position: absolute; left: 251px; top: 91px;
    font-family: "Questrial", sans-serif;
    font-size: 13px; line-height: 14.2px;
    color: var(--ink); list-style: none;
    white-space: nowrap;
  }
  .contact__label {
    display: inline-block; width: 19px;
    font-family: "Montserrat", sans-serif; font-weight: 700;
    font-size: 11px; color: var(--navy);
  }

  .signature {
    position: absolute; left: 17px; top: 138px;
    white-space: nowrap; line-height: 1;
  }
  .signature__name {
    font-family: "Montserrat", sans-serif; font-weight: 700;
    font-size: 19px; color: var(--navy);
  }
  .signature__role {
    font-family: "Questrial", sans-serif;
    font-size: 14px; color: var(--navy);
  }
</style>
</head>
<body>
<main class="canvas">
  <section class="card card--front" aria-label="Business card front">
    <div class="wordmark">Maple Roster</div>
    <div class="rule"></div>
    <ul class="contact">
      <li><span class="contact__label">T:</span> +64 21 555 0192</li>
      <li><span class="contact__label">E:</span> clara@mapleroster.nz</li>
      <li><span class="contact__label">W:</span> www.mapleroster.nz</li>
    </ul>
    <p class="signature">
      <span class="signature__name">Clara Whitford -</span>
      <span class="signature__role">Director &nbsp;|&nbsp; Senior Search Consultant</span>
    </p>
  </section>

  <section class="card card--back" aria-label="Business card back">
    <div class="wordmark">Maple Roster</div>
  </section>
</main>
</body>
</html>
```